13 Varno - new website design project

Our company Varno Electrical is developing a new lead generation website focused on Electrical, LED Lighting and Solar Power. We need a high converting website.

Example of our current website is www.varnoelectrical-example.com.au You can take content from this website for this new design. Our colours are red, black and white. For our new website we would like to promote Varno, Spark Every Day. Please listen to the jingle.

The below link is the company jingle that we have developed.
http://www.tunecraftdemo.com.au/vrn-tc-v1/

The key for this brief is to generate leads for Electrical, LED Lighting (for commercial) and Solar Power & Storage.

Target Market(s)

Business owners in Melbourne Victoria

Number of Pages Required

4 page

Colors
ec1f27
ffffff

Requirements
Must have
• This page must be clean, be in line with company branding and a high converting lead website.

```html
<!DOCTYPE html>
<html lang="en">
<head>
<meta charset="utf-8">
<title>Varno Electrical – Spark Every Day</title>
<link rel="stylesheet" href="https://fonts.googleapis.com/css2?family=Lato:wght@400;700;900&family=Open+Sans:wght@400;600;700&display=swap">
<style>
:root{
  --red:#ec1f27;
  --red-dark:#c9161d;
  --ink:#222222;
  --text:#555555;
  --muted:#777777;
  --line:#d6d6d6;
  --grey-band:#e2e2e2;
  --charcoal:#2b2e33;
  --white:#ffffff;
}
*{box-sizing:border-box;margin:0;padding:0}
html,body{width:1200px;height:2699px;overflow:hidden;background:var(--white)}
body{position:relative;font-family:"Open Sans",Arial,sans-serif;color:var(--text)}
.abs{position:absolute}
h1,h2,h3,h4{font-family:"Lato",Arial,sans-serif;color:var(--ink)}

/* header */
.topbar-red{left:0;top:0;width:620px;height:4px;background:var(--red)}
.topbar-dark{left:620px;top:0;width:580px;height:4px;background:var(--charcoal)}
.logo{left:100px;top:14px}
.logo-name{font-family:"Lato",sans-serif;font-weight:900;font-size:44px;color:var(--red);letter-spacing:1px;line-height:1}
.logo-tag{font-family:"Lato",sans-serif;font-weight:700;font-size:13px;color:var(--ink);margin-top:4px}
.contact-pill{top:14px;display:flex;align-items:center;gap:14px;font-size:15px;color:var(--ink);font-weight:600}
.pill-icon{width:34px;height:34px;border-radius:50%;border:1px solid var(--line);display:flex;align-items:center;justify-content:center}
.nav{left:356px;top:64px;display:flex;gap:0;font-family:"Lato",sans-serif;font-weight:700;font-size:14.5px;color:var(--ink)}
.nav a{text-decoration:none;color:inherit;padding:0 18px}
.nav a.active{color:var(--red)}

/* hero */
.hero{left:0;top:90px;width:1200px;height:435px;background:linear-gradient(180deg,#b98a52 0%,#d9a864 30%,#8e7452 55%,#2c3a4a 72%,#3d5a2c 100%)}
.hero-title{left:0;top:196px;width:1200px;text-align:center;font-family:"Lato",sans-serif;font-weight:700;font-size:62px;color:var(--white);text-shadow:0 2px 6px rgba(0,0,0,.35)}
.hero-sub{left:0;top:280px;width:1200px;text-align:center;font-size:17px;line-height:32px;color:var(--white);text-shadow:0 1px 3px rgba(0,0,0,.5)}
.btn{background:var(--red);color:var(--white);font-family:"Lato",sans-serif;font-weight:700;text-transform:uppercase;text-align:center}
.hero-btn{left:502px;top:373px;width:196px;height:38px;line-height:38px;font-size:15px}
.dots{left:532px;top:486px;display:flex;gap:6px}
.dots span{width:30px;height:4px;background:var(--white)}
.dots span.on{background:var(--red)}

/* welcome */
.welcome-title{left:98px;top:604px;font-size:26px;font-weight:700;letter-spacing:.3px}
.welcome-copy{left:98px;top:656px;width:490px;font-size:11.5px;line-height:25px;color:var(--text)}
.welcome-copy p+p{margin-top:10px}
.read-more{font-family:"Lato",sans-serif;font-weight:700;font-size:13px;color:var(--red)}
.video{left:620px;top:585px;width:482px;height:312px;border:4px solid var(--white);box-shadow:0 0 6px rgba(0,0,0,.3);background:linear-gradient(135deg,#3a4660 0%,#6b7c9a 40%,#d7c239 60%,#2b3650 100%)}
.video-bar{left:0;top:0;width:100%;height:30px;background:rgba(0,0,0,.55);color:var(--white);font-size:14px;font-weight:600;padding:6px 14px}
.play{left:212px;top:128px;width:50px;height:50px;border-radius:50%;background:rgba(0,0,0,.7)}

/* services */
.services{left:0;top:965px;width:1200px;height:345px;background:linear-gradient(180deg,#6f7377,#4a4e52)}
.service{top:0;width:380px;text-align:center;color:var(--white)}
.service-icon{margin-top:45px;height:80px}
.service h3{color:var(--white);font-size:20px;font-weight:700;margin-top:30px}
.service p{font-size:12.5px;line-height:24px;margin-top:12px}
.service .read-more{color:var(--white);display:block;margin-top:24px}

/* why */
.section-title{left:0;width:1200px;text-align:center;font-size:25px;font-weight:700}
.why{top:1426px;width:200px;text-align:center}
.why-icon{width:98px;height:98px;border-radius:50%;border:1px solid var(--line);margin:0 auto;display:flex;align-items:center;justify-content:center}
.why h4{font-family:"Open Sans",sans-serif;font-weight:400;font-size:15.5px;color:var(--ink);margin-top:16px}
.why p{font-size:11.5px;line-height:23px;color:var(--muted);margin-top:6px}
.divider{left:98px;top:1665px;width:1004px;height:1px;background:var(--line)}
.client{top:1787px;width:192px;height:108px;display:flex;align-items:center;justify-content:center;font-family:"Open Sans",sans-serif;font-weight:700;font-size:22px;color:var(--ink);text-align:center;line-height:1.2}

/* testimonial */
.testimonial{left:0;top:1960px;width:1200px;height:258px;background:var(--grey-band)}
.t-photo{left:98px;top:38px;width:274px;height:182px;border:3px solid var(--white);background:linear-gradient(180deg,#f2e23a 0%,#f2e23a 24%,#556373 25%,#8a939c 100%)}
.t-rule{left:410px;top:52px;width:1px;height:140px;background:#b9b9b9}
.t-quote{left:440px;top:74px;width:660px;font-size:13.5px;line-height:31px;font-style:italic;color:var(--text)}
.t-name{left:440px;top:158px;font-size:15px;color:var(--red);font-style:italic}
.t-name b{font-style:normal}
.t-arrow{top:114px}

/* contact */
.sub-title{font-family:"Lato",sans-serif;font-weight:700;font-size:17px;color:var(--ink)}
.field{height:33px;border:1px solid #cfcfcf;font-size:11px;color:var(--muted);padding:8px 12px}
.submit{left:588px;top:2550px;width:115px;height:38px;line-height:38px;font-size:14px}
.info-row{left:782px;display:flex;gap:22px;font-size:12px;line-height:24px;color:var(--text)}
.info-icon{width:38px;height:38px;border-radius:50%;border:1px solid var(--line);display:flex;align-items:center;justify-content:center;flex:none}

/* footer */
.footer-dark{left:0;top:2635px;width:1200px;height:64px;background:var(--charcoal)}
.copyright{left:98px;top:2657px;font-size:12px;color:var(--white)}
.social{top:2653px;width:28px;height:28px;border-radius:50%;border:1px solid rgba(255,255,255,.8)}
</style>
</head>
<body>

<!-- Header -->
<div class="abs topbar-red"></div>
<div class="abs topbar-dark"></div>
<div class="abs logo">
  <div class="logo-name">VARNO</div>
  <div class="logo-tag">Spark Every Day</div>
</div>
<div class="abs contact-pill" style="left:672px">
  <span class="pill-icon"><svg width="14" height="14" viewBox="0 0 24 24"><path fill="#ec1f27" d="M6.6 10.8a15.1 15.1 0 0 0 6.6 6.6l2.2-2.2c.3-.3.7-.4 1-.2 1.1.4 2.3.6 3.6.6.6 0 1 .4 1 1V20c0 .6-.4 1-1 1A17 17 0 0 1 3 4c0-.6.4-1 1-1h3.5c.6 0 1 .4 1 1 0 1.3.2 2.5.6 3.6.1.3 0 .7-.2 1z"/></svg></span>1300 555 274
</div>
<div class="abs contact-pill" style="left:842px">
  <span class="pill-icon"><svg width="14" height="14" viewBox="0 0 24 24"><path fill="#ec1f27" d="M2 5h20v14H2z"/><path fill="none" stroke="#fff" stroke-width="2" d="M2 6l10 7 10-7"/></svg></span>service@varnoelectrical-example.com.au
</div>
<nav class="abs nav">
  <a class="active">HOME</a><a>VARNO STORY</a><a>SERVICES</a><a>OUR WORK</a><a>SOLAR POWER</a><a>CONTACT US</a>
  <a><svg width="14" height="14" viewBox="0 0 24 24"><circle cx="10" cy="10" r="7" fill="none" stroke="#222" stroke-width="3"/><path d="M15 15l6 6" stroke="#222" stroke-width="3"/></svg></a>
</nav>

<!-- Hero -->
<div class="abs hero" role="img" aria-label="Sunset photo of solar panels, power pylons and a wind turbine"></div>
<h1 class="abs hero-title">Spark Every Day</h1>
<div class="abs hero-sub">Our company Varno Electrical is developing a new lead generation website<br>focused on Electrical, LED Lighting and Solar Power</div>
<div class="abs btn hero-btn">Get more info</div>
<div class="abs dots"><span class="on"></span><span></span><span></span><span></span></div>

<!-- Welcome -->
<h2 class="abs welcome-title">WELCOME TO VARNO ELECTRICAL</h2>
<div class="abs welcome-copy">
  <p>Electrical and Energy Solutions are at the forefront of our company. Varno Electrical has a long history in Electrical, LED Lighting and Solar Power and just like the Cougar, we will strive to be fierce &amp; agile in an effort to exceed our customer's expectations and develop stronger links with all our business partners &amp; community.</p>
  <p>Varno Electrical is an expert Electrical Company providing services to all Residential and Commercial customers.</p>
</div>
<div class="abs read-more" style="left:98px;top:862px">READ MORE &gt;&gt;</div>
<div class="abs video" role="img" aria-label="Video still of an electrician in hi-vis working on wiring">
  <div class="abs video-bar">Expert Electricity Contracting</div>
  <svg class="abs" style="right:12px;top:8px" width="40" height="14" viewBox="0 0 40 14"><circle cx="7" cy="7" r="5.5" fill="none" stroke="#fff" stroke-width="1.5"/><path d="M24 11c2-5 6-6 10-6V2l5 4.5-5 4.5V8c-4 0-7 1-10 3z" fill="#fff"/></svg>
  <div class="abs play"><svg width="50" height="50" viewBox="0 0 50 50"><path d="M20 15l16 10-16 10z" fill="#fff"/></svg></div>
</div>

<!-- Services -->
<div class="abs services" role="img" aria-label="Grey industrial warehouse ceiling background">
  <svg class="abs" style="left:0;top:0" width="1200" height="345"><polygon points="432,0 848,0 762,345 348,345" fill="#ec1f27"/></svg>
  <div class="abs service" style="left:8px">
    <svg class="service-icon" width="90" height="80" viewBox="0 0 90 80" fill="none" stroke="#fff" stroke-width="4" stroke-linecap="round"><path d="M50 8L34 42h16L38 72" stroke-linejoin="round"/><path d="M14 40h10M66 40h10M20 16l8 8M70 16l-8 8M20 64l8-8M70 64l-8-8"/></svg>
    <h3>ELECTRICAL</h3>
    <p>Varno Electrical has an expert team that will come<br>to your business, ensuring you get best advice.<br>Book in today to arrange your free</p>
    <span class="read-more">READ MORE &gt;&gt;</span>
  </div>
  <div class="abs service" style="left:410px">
    <svg class="service-icon" width="80" height="80" viewBox="0 0 80 80" fill="none" stroke="#fff" stroke-width="4" stroke-linecap="round" stroke-linejoin="round"><rect x="14" y="14" width="16" height="20" rx="2"/><path d="M18 14V6M26 14V6M22 34v10a18 18 0 0 0 36 0V34"/><rect x="50" y="14" width="16" height="20" rx="2"/><path d="M40 6l-5 10h8l-5 10"/></svg>
    <h3>LED LIGHTING</h3>
    <p>Varno Electrical has an expert team that will come<br>to your business, ensuring you get best advice.<br>Book in today to arrange your free</p>
    <span class="read-more">READ MORE &gt;&gt;</span>
  </div>
  <div class="abs service" style="left:818px">
    <svg class="service-icon" width="80" height="80" viewBox="0 0 80 80" fill="none" stroke="#fff" stroke-width="4" stroke-linejoin="round"><circle cx="40" cy="12" r="5"/><rect x="14" y="26" width="52" height="40" rx="3"/><path d="M14 40h52M14 53h52M31 26v40M49 26v40"/></svg>
    <h3>SOLAR POWER</h3>
    <p>Varno Electrical has an expert team that will come<br>to your business, ensuring you get best advice.<br>Book in today to arrange your free</p>
    <span class="read-more">READ MORE &gt;&gt;</span>
  </div>
</div>

<!-- Why choose us -->
<h2 class="abs section-title" style="top:1364px">WHY CHOOSE US?</h2>
<div class="abs why" style="left:85px">
  <div class="why-icon"><svg width="34" height="30" viewBox="0 0 34 30"><circle cx="12" cy="16" r="9" fill="none" stroke="#ec1f27" stroke-width="6" stroke-dasharray="4 3"/><circle cx="12" cy="16" r="3" fill="#ec1f27"/><circle cx="27" cy="8" r="5" fill="none" stroke="#ec1f27" stroke-width="4" stroke-dasharray="3 2"/></svg></div>
  <h4>Professional Service</h4><p>When you hire a Varno Electrical<br>Electrician you will get</p>
</div>
<div class="abs why" style="left:292px">
  <div class="why-icon"><svg width="28" height="28" viewBox="0 0 24 24"><path fill="#ec1f27" d="M2 10h4v12H2zM8 22V10l5-8c2 0 3 1 2.5 3L14 9h6c1.2 0 2 1 1.8 2.2l-1.5 8.5c-.2 1.3-1.2 2.3-2.5 2.3z"/></svg></div>
  <h4>5 year Guarantee</h4><p>When you hire a Varno Electrical<br>Electrician you will get</p>
</div>
<div class="abs why" style="left:500px">
  <div class="why-icon"><svg width="32" height="24" viewBox="0 0 32 24"><rect x="1" y="2" width="30" height="20" fill="#ec1f27"/><rect x="5" y="6" width="22" height="12" fill="none" stroke="#fff" stroke-width="1.5"/><circle cx="16" cy="12" r="4" fill="#fff"/></svg></div>
  <h4>Value for Money</h4><p>When you hire a Varno Electrical<br>Electrician you will get</p>
</div>
<div class="abs why" style="left:707px">
  <div class="why-icon"><svg width="30" height="28" viewBox="0 0 30 28" fill="none" stroke="#ec1f27" stroke-width="4" stroke-linejoin="round"><path d="M9 12l5-9 5 9M24 14l3 6H15M6 14l-3 6h9"/></svg></div>
  <h4>Environmentally friendly</h4><p>When you hire a Varno Electrical<br>Electrician you will get</p>
</div>
<div class="abs why" style="left:915px">
  <div class="why-icon"><svg width="30" height="30" viewBox="0 0 30 30"><circle cx="15" cy="15" r="14" fill="#ec1f27"/><path d="M8 15l5 5 9-10" fill="none" stroke="#fff" stroke-width="3.5"/></svg></div>
  <h4>Fully insured</h4><p>When you hire a Varno Electrical<br>Electrician you will get</p>
</div>
<div class="abs divider"></div>

<!-- Clients -->
<h2 class="abs section-title" style="top:1706px">OUR SATISFIED CLIENTS INCLUDE...</h2>
<div class="abs client" style="left:123px">Heron Plumbing<br>Supplies</div>
<div class="abs client" style="left:372px">Brightmart</div>
<div class="abs client" style="left:623px">Outback Gear<br>Stores</div>
<div class="abs client" style="left:876px">Burger<br>Harbour</div>

<!-- Testimonial -->
<div class="abs testimonial">
  <svg class="abs t-arrow" style="left:36px" width="16" height="28" viewBox="0 0 16 28"><path d="M14 2L3 14l11 12" fill="none" stroke="#fff" stroke-width="3"/></svg>
  <svg class="abs t-arrow" style="left:1148px" width="16" height="28" viewBox="0 0 16 28"><path d="M2 2l11 12L2 26" fill="none" stroke="#fff" stroke-width="3"/></svg>
  <div class="abs t-photo" role="img" aria-label="Photo of a client's outdoor gear store interior"></div>
  <div class="abs t-rule"></div>
  <div class="abs t-quote">The service, communication and after sales service of Varno Electrical has been awesome. We would strongly recommend them to any business contemplating upgrading their lighting or any other electrical work.</div>
  <div class="abs t-name"><b>- Daniel Whitmore,</b> Executive Outback Gear Stores</div>
</div>

<!-- Contact -->
<h2 class="abs section-title" style="top:2277px">CONTACT US</h2>
<div class="abs sub-title" style="left:98px;top:2347px">Get In Touch:</div>
<div class="abs field" style="left:98px;top:2393px;width:297px">Name :</div>
<div class="abs field" style="left:407px;top:2393px;width:296px">Email :</div>
<div class="abs field" style="left:98px;top:2437px;width:297px">Phone :</div>
<div class="abs field" style="left:407px;top:2437px;width:296px">Purpose :
  <svg class="abs" style="right:0;top:0" width="36" height="31"><path d="M1 0v31" stroke="#cfcfcf"/><path d="M14 13l4 5 4-5z" fill="#888"/></svg>
</div>
<div class="abs field" style="left:98px;top:2480px;width:605px;height:60px">Message :</div>
<div class="abs btn submit">Submit
  <svg class="abs" style="right:0;top:0" width="22" height="38"><polygon points="0,0 22,0 22,38" fill="#2b2e33"/></svg>
</div>

<div class="abs sub-title" style="left:782px;top:2347px">Contact Information</div>
<div class="abs info-row" style="top:2394px">
  <span class="info-icon"><svg width="14" height="18" viewBox="0 0 14 18"><path d="M7 0a7 7 0 0 1 7 7c0 5-7 11-7 11S0 12 0 7a7 7 0 0 1 7-7z" fill="#ec1f27"/><circle cx="7" cy="7" r="2.5" fill="#fff"/></svg></span>
  <span>8/42 Carrow Rd<br>Glen Ashby<br>VIC 3150</span>
</div>
<div class="abs info-row" style="top:2482px">
  <span class="info-icon"><svg width="14" height="14" viewBox="0 0 24 24"><path fill="#ec1f27" d="M6.6 10.8a15.1 15.1 0 0 0 6.6 6.6l2.2-2.2c.3-.3.7-.4 1-.2 1.1.4 2.3.6 3.6.6.6 0 1 .4 1 1V20c0 .6-.4 1-1 1A17 17 0 0 1 3 4c0-.6.4-1 1-1h3.5c.6 0 1 .4 1 1 0 1.3.2 2.5.6 3.6.1.3 0 .7-.2 1z"/></svg></span>
  <span style="line-height:38px">1300 555 274</span>
</div>
<div class="abs info-row" style="top:2546px">
  <span class="info-icon"><svg width="14" height="14" viewBox="0 0 24 24"><path fill="#ec1f27" d="M2 5h20v14H2z"/><path fill="none" stroke="#fff" stroke-width="2" d="M2 6l10 7 10-7"/></svg></span>
  <span style="line-height:38px">service@varnoelectrical-example.com.au</span>
</div>

<!-- Footer -->
<div class="abs footer-dark"></div>
<svg class="abs" style="left:0;top:2635px" width="660" height="64"><polygon points="0,0 620,0 660,64 0,64" fill="#ec1f27"/></svg>
<div class="abs copyright">Copyrights © 2017, Varno Electrical. All rights reserved.</div>
<div class="abs social" style="left:976px"></div>
<div class="abs social" style="left:1010px"></div>
<div class="abs social" style="left:1044px"></div>
<div class="abs social" style="left:1078px"></div>

</body>
</html>
```